Business Cards Design for the electrical wholesaler: clean bold dynamic :)

We need a business card design that would follow our latest brand guidelines. As an electrical wholesaler we want to bring a fresh look and feel into the industry. The design should be clean bold and dynamic. It should come alive with the renewed energy of our green colour. Our grey colour should keep things balanced and complement the notion of maturity and responsibility. We employ Lato as a corporate font however are not bound by this font and we’re open to interpretation here.

Target Market(s)

Electrical contractors

Industry/Entity Type

Business

Contact Information for Business Card

Logo
Name & Surname: Halyna Dorosh
Job Title: Director of Marketing
Email: halya.dorosh@quillmail.example
Cell phone: XXX.XXX.XXXX
Address: 20517 - 87 Ave. Edmonton, AB, Canada. T6K 4N8
Business Phone: 780.555.0184
Website: www.brovix.example

Font styles to use
Other font styles liked:
• Lato

Requirements
Must have
• Logo & website
Nice to have
• Brand elements - some of them you may find in the attached Brand Guidelines (e.g. three lines on the background signifying "W")

```html
<!DOCTYPE html>
<html lang="en">
<head>
<meta charset="utf-8">
<title>brovix business cards</title>
<link rel="stylesheet" href="https://fonts.googleapis.com/css2?family=Roboto:wght@400;500&display=swap">
<style>
  :root {
    --backdrop: #b9b9b9;
    --green: #7ab626;
    --green-deep: #64a823;
    --charcoal: #4a4d50;
    --paper: #f3f3f3;
    --ink: #3f4245;
    --white: #ffffff;
  }
  * { margin: 0; padding: 0; box-sizing: border-box; }
  html, body {
    width: 1200px; height: 576px; overflow: hidden;
    background: var(--backdrop);
    font-family: "Roboto", Arial, sans-serif;
  }
  .stage { position: relative; width: 1200px; height: 576px; }
  .card {
    position: absolute; top: 138px;
    width: 484px; height: 294px;
    border-radius: 14px; overflow: hidden;
  }
  .card-front {
    left: 82px;
    background: linear-gradient(160deg, var(--green) 0%, var(--green-deep) 100%);
  }
  .card-back { left: 600px; background: var(--paper); }

  .brand {
    display: flex; align-items: center; gap: 8px;
    position: absolute; font-weight: 500; line-height: 1;
  }
  .brand-mark { display: block; }
  .card-front .brand {
    top: 122px; left: 50%; transform: translateX(-50%);
    font-size: 46px; color: var(--charcoal);
  }
  .card-front .brand-mark { width: 30px; height: 30px; background: var(--white); }
  .card-back .brand {
    top: 36px; left: 27px;
    font-size: 40px; color: var(--charcoal);
  }
  .card-back .brand-mark { width: 26px; height: 26px; background: var(--green); }

  .info-band {
    position: absolute; left: 0; top: 114px;
    width: 100%; height: 135px;
    background: var(--charcoal);
  }
  .person-name {
    position: absolute; left: 27px; top: 31px;
    font-size: 20px; font-weight: 500; color: var(--green);
  }
  .person-role {
    position: absolute; left: 27px; top: 57px;
    font-size: 12px; color: var(--paper);
  }
  .contact-list {
    position: absolute; left: 27px; top: 81px;
    list-style: none; font-size: 12px; color: var(--paper);
  }
  .contact-list li { display: flex; align-items: center; gap: 6px; height: 16px; }
  .contact-row { gap: 6px; }
  .contact-row span { display: flex; align-items: center; gap: 6px; margin-right: 4px; }
  .contact-icon { width: 11px; height: 11px; flex: none; }
  .accent { color: var(--green); }
  .address {
    position: absolute; left: 27px; top: 263px;
    font-size: 12px; color: var(--ink);
  }
</style>
</head>
<body>
<main class="stage">
  <section class="card card-front" aria-label="Card front">
    <div class="brand"><span class="brand-mark"></span>brovix</div>
  </section>

  <section class="card card-back" aria-label="Card back">
    <div class="brand"><span class="brand-mark"></span>brovix</div>

    <div class="info-band">
      <h1 class="person-name">Halyna Dorosh</h1>
      <p class="person-role">Founder &amp; CEO</p>
      <ul class="contact-list">
        <li>
          <svg class="contact-icon" viewBox="0 0 12 12" aria-hidden="true">
            <circle cx="6" cy="6" r="5.5" fill="none" stroke="#7ab626"/>
            <path d="M3.6 3.4h1.4l.6 1.4-.8.6a4 4 0 0 0 1.8 1.8l.6-.8 1.4.6v1.4c-3 .3-5.3-2-5-5z" fill="#7ab626"/>
          </svg>
          +1 780-555-0184
        </li>
        <li class="contact-row">
          <span>
            <svg class="contact-icon" viewBox="0 0 12 12" aria-hidden="true">
              <circle cx="6" cy="6" r="5.5" fill="none" stroke="#7ab626"/>
              <rect x="3" y="4" width="6" height="4.2" fill="#7ab626"/>
              <path d="M3 4l3 2.3L9 4" fill="none" stroke="#4a4d50" stroke-width=".7"/>
            </svg>
            hello@brovix.example
          </span>
          <span>
            <svg class="contact-icon" viewBox="0 0 12 12" aria-hidden="true">
              <circle cx="6" cy="6" r="5.5" fill="none" stroke="#7ab626"/>
              <circle cx="6" cy="6" r="3" fill="#7ab626"/>
            </svg>
            www.<span class="accent" style="margin:0">brovix</span>.example
          </span>
        </li>
      </ul>
    </div>

    <p class="address">20517 - 87 Ave. Edmonton, AB, Canada T6K 4N8</p>
  </section>
</main>
</body>
</html>
```